Varentoria Business Card and Letter Head

We are a leadership assessment consultancy based in Sydney, Australia. We help executive-level decison-makers select leaders for more senior level roles in corporate and government organisations. Our methodology is based on the latest research from the field of neuroscience.
We need a business card design and matching letter head that presents our company, Varentoria, as a:
1. trusted adviser to senior executive-level decison makers
2. niche consultancy who are experts in the field of assessing leadership talent
3. results-focused solution provider who balance scientific methods with pragmatic solutions
The following company details should be used in all designs:
Company Name: Varentoria
Details (for business card):
Derek Hanford
Prime Capacity Officer
Level 14, Marlow Tower
7 Marlow Square
Sydney, NSW 2011 Australia
Phone: 1300 582 714
Mobile: 0412 637 258
Email: derek.hanford@varentoria-example.com.au
Website: varentoria-example.com.au
I have attached the logo for Varentoria (for both a white and black background) - your business card and letter head designs must incoporate this logo and colour scheme.
Thanks for your interest in this project, I'm looking forward to receiving your ideas.
Regards,
Derek
Target Market(s)
Executive-level decison-makers in corporate and government organisations (e.g., CEO, VP, Head of Human Resources)
Industry/Entity Type
Leadership
Look and feel

```html
<!DOCTYPE html>
<html lang="en">
<head>
<meta charset="utf-8">
<title>Varentoria Stationery</title>
<link href="https://fonts.googleapis.com/css2?family=Open+Sans:wght@400;600&family=PT+Sans+Narrow&family=Quicksand:wght@300;400&display=swap" rel="stylesheet">
<style>
:root{
  --backdrop:#ecebe8;
  --paper:#ffffff;
  --ink:#3a3a3c;
  --ink-soft:#6b6b6e;
  --charcoal:#3f3f42;
  --charcoal-light:#8c8c8f;
  --accent:#c0281c;
  --rule:#c9c9cc;
  --rule-dark:#9a9a9d;
  --on-dark:#e6e6e8;
}
*{box-sizing:border-box;margin:0;padding:0}
html,body{width:1200px;height:834px;overflow:hidden}
body{background:var(--backdrop);position:relative;font-family:"Open Sans",Arial,sans-serif;color:var(--ink)}
.piece{position:absolute;box-shadow:0 2px 6px rgba(0,0,0,.18)}
.paper{background:var(--paper)}
.dark{background:radial-gradient(ellipse at 50% 40%,var(--charcoal-light) 0%,var(--charcoal) 75%)}
.wordmark{display:flex;align-items:center;gap:7px;font-family:"Open Sans",Arial,sans-serif;font-weight:600;color:var(--ink);letter-spacing:-.2px;line-height:1;white-space:nowrap}
.wordmark .mark-square{background:var(--accent);flex:none}
.on-dark .wordmark{color:var(--on-dark)}
.tagline{font-family:"Open Sans",Arial,sans-serif;font-size:6px;letter-spacing:.6px;text-transform:uppercase;color:var(--ink-soft);white-space:nowrap}
.on-dark .tagline{color:#b9b9bc}
.address{font-family:"PT Sans Narrow","Arial Narrow",sans-serif;line-height:1.35;color:var(--ink);white-space:nowrap}
.on-dark .address{color:var(--on-dark)}

/* letterhead */
.letterhead{left:35px;top:38px;width:505px;height:715px}
.letterhead .head{position:absolute;top:20px;left:0;right:0;display:flex;flex-direction:column;align-items:center;gap:4px}
.letterhead .head .wordmark{font-size:24px}
.letterhead .head .mark-square{width:20px;height:20px}
.letterhead .head-rule{position:absolute;top:74px;left:10px;right:14px;height:2px;background:var(--rule)}
.letterhead .frame{position:absolute;left:10px;right:14px;top:74px;bottom:14px;border-right:2px solid var(--rule);border-bottom:2px solid var(--rule)}
.letterhead .footer{position:absolute;left:102px;bottom:28px;font-size:7.5px}
.letterhead .footer p+p{margin-top:9px}

/* business cards */
.card-front{left:109px;top:266px;width:272px;height:151px}
.card-front .rule{position:absolute;left:26px;right:10px;height:1px;background:var(--rule-dark)}
.card-front .logo{position:absolute;left:66px;top:56px}
.card-front .wordmark{font-size:19px}
.card-front .mark-square{width:16px;height:16px}
.card-back{left:233px;top:433px;width:268px;height:151px}
.card-back .inner{position:absolute;inset:6px;border:1px solid var(--rule)}
.card-back .name-row{position:absolute;left:120px;top:16px;display:flex;gap:5px}
.card-back .mark-square{width:11px;height:11px;background:var(--accent);margin-top:2px}
.card-back .person{font-weight:600;color:var(--accent);font-size:11px;line-height:1.1}
.card-back .role{font-size:7.5px;color:var(--accent);font-weight:400}
.card-back .address{position:absolute;left:120px;top:52px;font-size:7px}
.card-back .contacts{position:absolute;left:120px;top:82px;list-style:none;font-family:"PT Sans Narrow",sans-serif;font-size:7px;line-height:1.55}
.card-back .contacts li{display:flex;align-items:center;gap:5px;white-space:nowrap}
.card-back .contacts svg{width:6px;height:6px;fill:var(--accent)}

/* compliments slip */
.comp-slip{left:560px;top:18px;width:610px;height:200px}
.comp-slip .frame{position:absolute;left:10px;top:10px;right:10px;bottom:10px;border:1px solid var(--rule)}
.comp-slip .logo{position:absolute;left:80px;top:42px}
.comp-slip .wordmark{font-size:20px}
.comp-slip .mark-square{width:16px;height:16px}
.comp-slip .address{position:absolute;left:80px;top:88px;font-size:8px}
.comp-slip .greeting{position:absolute;left:330px;top:64px;font-family:"Quicksand",sans-serif;font-weight:300;font-size:19px;color:var(--accent);letter-spacing:.5px}

/* envelope */
.envelope{left:560px;top:232px;width:610px;height:250px}
.envelope .flap{position:absolute;left:0;top:0;width:610px;height:54px}
.envelope .body{position:absolute;left:0;top:54px;width:610px;height:196px}
.envelope .frame{position:absolute;left:12px;top:10px;right:12px;bottom:10px;border:1px solid var(--rule);border-left:none}
.envelope .flap-label{position:absolute;left:0;right:0;top:22px;text-align:center;font-size:8px;font-weight:600;color:#cfcfd2;letter-spacing:.6px}
.envelope .logo{position:absolute;left:105px;top:22px}
.envelope .wordmark{font-size:16px}
.envelope .mark-square{width:13px;height:13px}
.envelope .address{position:absolute;left:105px;top:60px;font-size:7.5px}

/* disc sleeve */
.sleeve{left:560px;top:500px;width:300px;height:300px}
.sleeve .rule{position:absolute;left:40px;right:12px;top:14px;height:1px;background:var(--rule-dark)}
.sleeve .logo{position:absolute;left:75px;top:92px}
.sleeve .wordmark{font-size:24px}
.sleeve .mark-square{width:20px;height:20px}
.sleeve .title{position:absolute;left:138px;top:196px;font-family:"Quicksand",sans-serif;font-weight:300;font-size:17px;color:var(--on-dark)}
.sleeve .address{position:absolute;left:138px;top:240px;font-size:7.5px}

/* disc */
.disc{left:880px;top:500px;width:300px;height:300px;border-radius:50%}
.disc .hole{position:absolute;left:115px;top:115px;width:70px;height:70px;border-radius:50%;background:var(--backdrop);box-shadow:inset 0 0 0 6px #5a5a5d}
.disc .logo{position:absolute;left:70px;top:56px}
.disc .wordmark{font-size:20px}
.disc .mark-square{width:16px;height:16px}
.disc .title{position:absolute;left:80px;top:210px;font-family:"Quicksand",sans-serif;font-weight:300;font-size:13px;color:var(--on-dark)}
.disc .address{position:absolute;left:80px;top:232px;font-size:6.5px}
</style>
</head>
<body>

<section class="piece paper letterhead" aria-label="Letterhead">
  <header class="head">
    <div class="wordmark"><span class="mark-square"></span>Varentoria</div>
    <div class="tagline">Assessing Executive Potential</div>
  </header>
  <div class="head-rule"></div>
  <div class="frame"></div>
  <footer class="footer address">
    <p>Level 14, Marlow Tower, 7 Marlow Square<br>Sydney, NSW 2011 Australia</p>
    <p>phone: 1300 582 714<br>mobile: 0412 637 258<br>email: derek.hanford@varentoria-example.com.au<br>website: varentoria-example.com.au</p>
  </footer>
</section>

<section class="piece dark on-dark card-front" aria-label="Business card front">
  <div class="rule" style="top:8px"></div>
  <div class="rule" style="bottom:8px"></div>
  <div class="logo">
    <div class="wordmark"><span class="mark-square"></span>Varentoria</div>
    <div class="tagline" style="margin:3px 0 0 23px">Assessing Executive Potential</div>
  </div>
</section>

<section class="piece paper card-back" aria-label="Business card back">
  <div class="inner"></div>
  <div class="name-row">
    <span class="mark-square"></span>
    <div><div class="person">Derek Hanford</div><div class="role">Prime Capacity Officer</div></div>
  </div>
  <p class="address">Level 14, Marlow Tower, 7 Marlow Square<br>Sydney, NSW 2011 Australia</p>
  <ul class="contacts">
    <li><svg viewBox="0 0 10 10"><path d="M2 0h2l1 3-1.5 1a6 6 0 0 0 2.5 2.5L7 5l3 1v2c0 1-1 2-2 2C4 10 0 6 0 2 0 1 1 0 2 0z"/></svg>1300 582 714</li>
    <li><svg viewBox="0 0 10 10"><rect x="2" y="0" width="6" height="10" rx="1"/></svg>0412 637 258</li>
    <li><svg viewBox="0 0 10 10"><rect x="0" y="2" width="10" height="6"/></svg>derek.hanford@varentoria-example.com.au</li>
    <li><svg viewBox="0 0 10 10"><circle cx="5" cy="5" r="5"/></svg>varentoria-example.com.au</li>
  </ul>
</section>

<section class="piece paper comp-slip" aria-label="Compliments slip">
  <div class="frame"></div>
  <div class="logo">
    <div class="wordmark"><span class="mark-square"></span>Varentoria</div>
    <div class="tagline" style="margin:3px 0 0 23px">Assessing Executive Potential</div>
  </div>
  <p class="address">Level 14, Marlow Tower<br>7 Marlow Square<br>Sydney, NSW 2011 Australia</p>
  <p class="greeting">With Compliments</p>
</section>

<section class="piece envelope" aria-label="DL envelope">
  <svg class="flap" viewBox="0 0 610 54" preserveAspectRatio="none">
    <defs><radialGradient id="flapShade" cx="50%" cy="60%" r="60%"><stop offset="0" stop-color="#a3a3a6"/><stop offset="1" stop-color="#3f3f42"/></radialGradient></defs>
    <path d="M0 54 L0 40 Q305 -20 610 40 L610 54 Z" fill="url(#flapShade)"/>
  </svg>
  <div class="flap-label">VARENTORIA</div>
  <div class="body paper">
    <div class="frame"></div>
    <div class="logo">
      <div class="wordmark"><span class="mark-square"></span>Varentoria</div>
      <div class="tagline" style="margin:3px 0 0 20px;font-size:5px">Assessing Executive Potential</div>
    </div>
    <p class="address">Level 14, Marlow Tower, 7 Marlow Square<br>Sydney, NSW 2011 Australia</p>
  </div>
</section>

<section class="piece dark on-dark sleeve" aria-label="Disc sleeve">
  <div class="rule"></div>
  <div class="logo">
    <div class="wordmark"><span class="mark-square"></span>Varentoria</div>
    <div class="tagline" style="margin:4px 0 0 27px;font-size:7px">Assessing Executive Potential</div>
  </div>
  <p class="title">Your Title Here</p>
  <p class="address">Level 14, Marlow Tower, 7 Marlow Square<br>Sydney, NSW 2011 Australia<br><br>derek.hanford@varentoria-example.com.au<br>varentoria-example.com.au</p>
</section>

<section class="piece dark on-dark disc" aria-label="Disc label">
  <div class="logo">
    <div class="wordmark"><span class="mark-square"></span>Varentoria</div>
    <div class="tagline" style="margin:3px 0 0 23px">Assessing Executive Potential</div>
  </div>
  <div class="hole"></div>
  <p class="title">Your Title Here</p>
  <p class="address">Level 14, Marlow Tower, 7 Marlow Square<br>Sydney, NSW 2011 Australia<br>varentoria-example.com.au</p>
</section>

</body>
</html>
```